holloway paving service

Needs to have phone number 0418259730 and email markholloway@brightmail.com.au.
ABN 62318470915
name mark holloway

For all your concreting solutions
Excavation
Exposed & colour concrete
House & shed slabs
Driveways
Landing & steps

Contact Information for Business Card

ph 0418259730
email markholloway@brightmail.com.au.
ABN 62318470915
name mark holloway

```html
<!DOCTYPE html>
<html lang="en">
<head>
<meta charset="utf-8">
<title>Holloway Paving Service – Business Card</title>
<link rel="stylesheet" href="https://fonts.googleapis.com/css2?family=Roboto:wght@400;500;700&display=swap">
<style>
  :root {
    --page-bg: #e9e7e4;
    --red-light: #f0562a;
    --red-dark: #c8260f;
    --charcoal: #2f2f31;
    --charcoal-dark: #1f1f21;
    --silver-light: #f4f4f4;
    --silver-dark: #b9bcbf;
    --diamond-edge: #262628;
    --text-light: #ffffff;
    --text-soft: #fbe3da;
    --brand-red: #d8361a;
    --brand-dark: #2a2a2c;
  }
  * { margin: 0; padding: 0; box-sizing: border-box; }
  html, body {
    width: 1200px;
    height: 969px;
    overflow: hidden;
    background: var(--page-bg);
    font-family: "Roboto", Arial, sans-serif;
  }
  .business-card {
    position: absolute;
    left: 100px;
    top: 200px;
    width: 1000px;
    height: 569px;
    overflow: hidden;
    box-shadow: 0 18px 40px rgba(0,0,0,0.18);
  }
  .card-background {
    position: absolute;
    inset: 0;
    width: 100%;
    height: 100%;
  }
  .contact-side {
    position: absolute;
    left: 60px;
    top: 66px;
    color: var(--text-light);
  }
  .holder-name {
    font-size: 32px;
    font-weight: 500;
    letter-spacing: 0.5px;
    text-transform: uppercase;
    margin-bottom: 26px;
  }
  .contact-list {
    list-style: none;
    font-size: 22px;
    line-height: 32px;
  }
  .contact-abn { margin-top: 26px; }
  .service-list {
    list-style: none;
    position: absolute;
    left: 60px;
    top: 358px;
    color: var(--text-soft);
    font-size: 22px;
    line-height: 30px;
  }
  .service-list li::before {
    content: "";
    display: inline-block;
    width: 8px;
    height: 8px;
    background: currentColor;
    transform: rotate(45deg);
    margin: 0 12px 4px 4px;
  }
  .brand-block {
    position: absolute;
    left: 628px;
    top: 236px;
    display: flex;
    align-items: center;
    gap: 16px;
  }
  .brand-square {
    width: 34px;
    height: 34px;
    background: var(--brand-red);
    flex: none;
  }
  .brand-name {
    color: var(--brand-red);
    font-size: 23px;
    font-weight: 700;
    line-height: 27px;
    text-transform: uppercase;
    letter-spacing: 0.5px;
  }
  .brand-phone {
    position: absolute;
    left: 678px;
    top: 306px;
    color: var(--brand-dark);
    font-size: 20px;
    font-weight: 500;
    letter-spacing: 2px;
  }
</style>
</head>
<body>
  <div class="business-card">
    <svg class="card-background" viewBox="0 0 1000 569" aria-hidden="true">
      <defs>
        <linearGradient id="redPanel" x1="0" y1="0" x2="1" y2="0.4">
          <stop offset="0" stop-color="var(--red-light)"/>
          <stop offset="1" stop-color="var(--red-dark)"/>
        </linearGradient>
        <linearGradient id="darkPanel" x1="0" y1="0" x2="0" y2="1">
          <stop offset="0" stop-color="var(--charcoal)"/>
          <stop offset="1" stop-color="var(--charcoal-dark)"/>
        </linearGradient>
        <linearGradient id="silverFace" x1="0" y1="0" x2="1" y2="1">
          <stop offset="0" stop-color="var(--silver-dark)"/>
          <stop offset="0.45" stop-color="var(--silver-light)"/>
          <stop offset="1" stop-color="var(--silver-dark)"/>
        </linearGradient>
      </defs>
      <rect class="red-panel" width="1000" height="569" fill="url(#redPanel)"/>
      <polygon class="dark-panel" points="681,0 1000,0 1000,569 681,569 779,471 1072,284 779,97" fill="url(#darkPanel)"/>
      <polygon class="diamond-edge" points="681,0 1072,284 681,569 381,284" fill="var(--diamond-edge)"/>
      <polygon class="diamond-face" points="681,16 1050,284 681,553 403,284" fill="url(#silverFace)"/>
    </svg>

    <div class="contact-side">
      <h1 class="holder-name">Mark Holloway</h1>
      <ul class="contact-list">
        <li>0418259730</li>
        <li>markholloway@brightmail.com.au</li>
        <li>www.hollowaypaving.com.au</li>
        <li class="contact-abn">ABN 62318470915</li>
      </ul>
    </div>

    <ul class="service-list">
      <li>Excavation</li>
      <li>Exposed &amp; colour concrete</li>
      <li>House &amp; shed slabs</li>
      <li>Driveways</li>
      <li>Landing &amp; steps</li>
    </ul>

    <div class="brand-block">
      <span class="brand-square"></span>
      <span class="brand-name">Holloway Paving<br>Service</span>
    </div>
    <div class="brand-phone">0418259730</div>
  </div>
</body>
</html>
```